Design for a newly formed Real Estate Management Company - Velmora Management

Background
Velmora Management is a Real Estate Company that manages properties for a small family business. I'd like to showcase the properties that I've acquired and turned around so they're performing well. This website will be a way for me to promote my business.

Different Sections
This website will help promote the work that I've been doing so it should include an About Us page. There should also be a page that goes through the different properties that we've managed and turned around. It would be great to have a design that allows me to visually show the different buildings that may be in various areas in a creative fashion. Finally, I need a section for a blog where I write about certain things prospective property owners should know about.

Design
http://www.quendal7.example/ is a good example of the type of design I'm looking for. For the about us page, I'd like it to be able to show a portrait photo and a section to give some information about the person. I will be adding more people to the team so if there's a way to easily add photos and descriptions of new members, that would be great.

Target Market(s)

Third Party Real Estate Servicers (i.e. Insurance, Mortgage Brokers, Brokers)
Investors who are thinking to invest with us
Tenants who want to see how well we manage properties

Industry/Entity Type

Real Estate

Number of Pages Required

3 page

Requirements
Must have
• Integration of the logo into the design of the website would be a must. I'd like the design to flow together well and not be pages kind of stitched together. There should also be a way for me to easily add properties to the list. I should be able to monitor the people that join the website and obtain a login. It would be great to be able to edit and add things to the design so things aren't hardcoded.
Nice to have
• Allow tenants to write reviews of their experience at the property. Should not be anonymous, they would need to log in so at least their first name will show. Blog should also have log in so they may comment on the posts.

```html
<!DOCTYPE html>
<html lang="en">
<head>
<meta charset="utf-8">
<title>Velmora Management</title>
<link href="https://fonts.googleapis.com/css2?family=Cinzel:wght@400;700&family=Open+Sans:wght@400;600;700&display=swap" rel="stylesheet">
<style>
:root{
  --blue:#2f86d1;
  --blue-dark:#2748a3;
  --blue-sky:#3a8fd6;
  --ink:#2b2b2b;
  --muted:#6d6d6d;
  --line:#e1e1e1;
  --white:#ffffff;
  --panel:rgba(28,26,26,.78);
}
*{box-sizing:border-box;margin:0;padding:0}
html,body{width:1200px;height:3077px;overflow:hidden}
body{font-family:"Open Sans",Arial,sans-serif;color:var(--ink);background:var(--white);position:relative}

/* header */
.site-header{position:absolute;top:0;left:0;width:1200px;height:98px;background:var(--white)}
.brand{position:absolute;left:98px;top:30px;display:flex;align-items:center;gap:10px}
.brand-mark{width:34px;height:34px;background:var(--blue-dark)}
.brand-name{font-family:"Cinzel",Georgia,serif;color:var(--blue-dark);font-size:22px;line-height:1}
.brand-name small{display:block;font-size:10px;letter-spacing:3px;margin-top:3px}
.main-nav{position:absolute;left:338px;top:40px;display:flex;gap:21px;font-family:"Cinzel",Georgia,serif;font-size:13.5px;color:#222}
.main-nav .active{color:var(--blue);position:relative;padding-left:12px}
.main-nav .active::before{content:"";position:absolute;left:0;top:-9px;width:6px;height:36px;border:4px solid var(--blue);border-right:none}
.search-icon{position:absolute;left:868px;top:42px}
.call-box{position:absolute;left:902px;top:26px;width:30px;height:46px;border:3px solid var(--blue);border-radius:5px}
.call-box::after{content:"";position:absolute;left:8px;bottom:3px;width:8px;height:3px;background:var(--blue)}
.call-label{position:absolute;left:952px;top:28px;font-family:"Cinzel",Georgia,serif;font-size:11px;color:#888;letter-spacing:1px}
.call-number{position:absolute;left:952px;top:45px;font-family:"Cinzel",Georgia,serif;font-size:21px;color:#333}
.header-rule{position:absolute;left:902px;top:0;width:200px;height:4px;background:var(--blue)}

/* hero */
.hero{position:absolute;top:98px;left:0;width:1200px;height:431px;overflow:hidden}
.hero-photo{position:absolute;inset:0;background:
  radial-gradient(ellipse 220px 160px at 600px 110px,rgba(214,186,140,.55),transparent 70%),
  radial-gradient(ellipse 300px 120px at 420px 420px,rgba(230,210,170,.45),transparent 70%),
  linear-gradient(180deg,rgba(0,0,0,.05) 0%,rgba(0,0,0,0) 50%,rgba(20,14,10,.35) 100%),
  linear-gradient(100deg,#3e3027 0%,#6e5c49 28%,#9b8870 46%,#6a5846 62%,#4a3b2f 78%,#3a2f27 100%)}
.hero-kicker{position:absolute;left:98px;top:172px;font-family:"Cinzel",Georgia,serif;color:#fff;font-size:27px;letter-spacing:2px}
.hero-title{position:absolute;left:98px;top:206px;font-family:"Cinzel",Georgia,serif;color:#fff;font-size:44px;letter-spacing:1px}
.dots{position:absolute;display:flex;gap:4px}
.dots span{width:16px;height:11px;border-radius:6px;border:2px solid #fff;background:transparent}
.dots span.on{background:var(--blue)}
.hero .dots{left:98px;top:381px}
.consult{position:absolute;left:738px;top:0;width:360px;height:431px;background:var(--panel)}
.consult h2{position:absolute;left:0;top:16px;width:100%;font-family:"Cinzel",Georgia,serif;color:#fff;font-weight:400;font-size:22px;text-align:center;letter-spacing:1px}
.field{position:absolute;left:17px;width:328px;height:35px;background:#fff;font-size:11px;color:#555;padding:10px 12px}
.field.select::after{content:"";position:absolute;right:0;top:0;width:32px;height:35px;background:#e2e2e2}
.field.select::before{content:"";position:absolute;right:11px;top:15px;border:5px solid transparent;border-top:6px solid #666;z-index:1}
.prompt{position:absolute;left:17px;top:290px;font-size:11px;line-height:14px;color:#fff}
.submit{position:absolute;left:17px;top:361px;width:328px;height:46px;background:linear-gradient(#3e92d8,#2a6fb6);color:#fff;font-weight:700;font-size:14px;text-align:center;line-height:46px;letter-spacing:1px}

/* section heading */
.sec-title{position:absolute;font-family:"Cinzel",Georgia,serif;font-weight:400;font-size:18px;letter-spacing:.5px;padding-left:22px;height:44px;line-height:54px;white-space:nowrap}
.sec-title::before{content:"";position:absolute;left:0;top:0;width:26px;height:40px;border-left:6px solid currentColor;border-top:6px solid currentColor}
.sec-title::after{content:"";position:absolute;left:0;bottom:0;width:40px;height:4px;background:currentColor}

/* welcome */
.welcome{position:absolute;top:529px;left:0;width:1200px;height:353px}
.welcome .sec-title{left:98px;top:42px;color:#222}
.welcome p{position:absolute;left:98px;width:525px;font-size:11.5px;line-height:2.1;color:#555}
.read-more{position:absolute;font-size:11.5px;font-weight:700;color:var(--blue)}
.welcome-photo{position:absolute;left:677px;top:41px;width:423px;height:271px;border:4px solid #fff;box-shadow:0 0 0 1px #ddd;background:
  radial-gradient(ellipse 140px 120px at 300px 70px,rgba(210,230,200,.8),transparent 70%),
  linear-gradient(180deg,transparent 55%,rgba(80,62,50,.75) 80%,#4a3c33 100%),
  linear-gradient(100deg,#7d8a74 0%,#c8cfc4 35%,#e4e6e1 55%,#a8b3a0 75%,#6b6a60 100%)}

/* featured */
.featured{position:absolute;top:882px;left:0;width:1200px;height:626px;background:linear-gradient(180deg,#3787cf,#3b92da 60%,#3a8dd4);overflow:hidden}
.featured .sec-title{left:478px;top:34px;color:#fff}
.slide{position:absolute;border:4px solid #fff;box-shadow:0 4px 14px rgba(0,0,0,.25)}
.featured .dots{left:570px;top:574px}

/* team */
.team{position:absolute;top:1508px;left:0;width:1200px;height:412px;background:linear-gradient(180deg,#2a4ea8,#25459d);overflow:hidden}
.team .sec-title{left:514px;top:34px;color:#fff}
.member{position:absolute;top:133px;width:190px;text-align:center;color:#fff}
.portrait{width:178px;height:178px;margin:0 auto;border-radius:50%;border:6px solid #fff}
.member h3{font-family:"Cinzel",Georgia,serif;font-weight:700;font-size:15px;margin-top:18px;letter-spacing:1px}
.member span{font-size:11.5px}
.arrow{position:absolute;top:215px}

/* blog & press */
.news{position:absolute;top:1920px;left:0;width:1200px;height:582px}
.news .sec-title{color:#222;top:36px}
.post{position:absolute;width:468px;height:124px;border-bottom:1px solid var(--line)}
.post.last{border-bottom:none}
.thumb{position:absolute;left:0;top:0;width:123px;height:103px;border:3px solid #fff;box-shadow:0 0 0 1px #ddd}
.post h4{position:absolute;left:147px;top:4px;width:320px;font-size:11.5px;font-weight:700;line-height:1.85;text-transform:uppercase;color:#222}
.meta{position:absolute;left:147px;top:60px;font-size:10.5px;color:var(--blue);display:flex;gap:8px;align-items:center}
.meta i{display:inline-block;width:9px;height:9px;background:var(--blue);border-radius:2px}
.view-more{position:absolute;top:525px;font-size:11.5px;font-weight:700;color:var(--blue)}

/* contact */
.contact{position:absolute;top:2502px;left:0;width:1200px;height:575px;background:linear-gradient(180deg,#333,#262626);color:#fff}
.contact .sec-title{left:478px;top:36px;color:#fff}
.contact h5{position:absolute;font-size:13.5px;font-weight:700;letter-spacing:.3px}
.contact label{position:absolute;left:98px;font-size:10.5px}
.input{position:absolute;left:98px;width:630px;background:#fff}
.send{position:absolute;left:636px;top:431px;width:92px;height:41px;border:1px solid #fff;font-size:12px;font-weight:700;text-align:center;line-height:39px}
.info-icon{position:absolute;left:810px;width:34px;height:34px;border-radius:50%;border:2px solid #fff;display:flex;align-items:center;justify-content:center}
.info-text{position:absolute;left:888px;font-size:11px;line-height:2.1}
.social{position:absolute;top:431px;left:810px;display:flex;gap:16px}
.social span{width:28px;height:28px;background:#fff;border-radius:3px}
.footer-rule{position:absolute;left:98px;top:503px;width:1004px;height:1px;background:#555}
.copyright{position:absolute;top:530px;width:1200px;text-align:center;font-size:11px;color:#ddd}
</style>
</head>
<body>

<header class="site-header">
  <div class="header-rule"></div>
  <div class="brand"><div class="brand-mark"></div><div class="brand-name">Velmora<small>MANAGEMENT</small></div></div>
  <nav class="main-nav">
    <span class="active">Home</span><span>About Us</span><span>Properties</span><span>Team</span><span>Blog</span><span>Press</span><span>Contact Us</span>
  </nav>
  <svg class="search-icon" width="14" height="14" viewBox="0 0 14 14"><circle cx="6" cy="6" r="4.2" fill="none" stroke="#222" stroke-width="2"/><line x1="9" y1="9" x2="13" y2="13" stroke="#222" stroke-width="2"/></svg>
  <div class="call-box"></div>
  <div class="call-label">Call Us Now</div>
  <div class="call-number">1 555 014 2290</div>
</header>

<section class="hero">
  <div class="hero-photo" role="img" aria-label="Warm interior of a furnished living space with bookshelves and pendant lights"></div>
  <div class="hero-kicker">PROPERTIES FOR A</div>
  <div class="hero-title">SMALL FAMILY BUSINESS</div>
  <div class="dots"><span class="on"></span><span></span><span></span><span></span></div>
  <form class="consult">
    <h2>FREE CONSULTATION</h2>
    <div class="field" style="top:66px">Name :</div>
    <div class="field" style="top:111px">Email :</div>
    <div class="field" style="top:156px">Phone Number :</div>
    <div class="field select" style="top:201px">Contact Type :</div>
    <div class="field select" style="top:246px">Looking to :</div>
    <div class="prompt">How soon would you like to buy / sell / lease?*</div>
    <div class="field select" style="top:314px">Now</div>
    <div class="submit">SUBMIT</div>
  </form>
</section>

<section class="welcome">
  <h2 class="sec-title">WELCOME TO VELMORA MANAGEMENT</h2>
  <p style="top:112px">Nemo enim ipsam voluptatem quia voluptas sit aspernatur aut odit aut fugit, sed quia conse quuntur magni dolores eos qui ratione voluptatem sequi nesciunt. Neque porro quisquamq ui dolorem ipsum quia dolor sit amet, consectetur, adipisic.</p>
  <p style="top:212px">Sed quia non numquamelus modi tempora incidunt ut labore et dolore magnam aliquam qu aerat voluptatem. Ut enimad minima veniam, quis nostrum ...</p>
  <div class="read-more" style="left:98px;top:286px">READ MORE &gt;&gt;</div>
  <div class="welcome-photo" role="img" aria-label="Agent showing a bright furnished living room to a couple"></div>
</section>

<section class="featured">
  <h2 class="sec-title">FEATURED PROPERTIES</h2>
  <div class="slide" role="img" aria-label="Office corridor with white chairs" style="left:103px;top:164px;width:100px;height:336px;background:linear-gradient(90deg,#6f757a,#c9cdd0 50%,#9aa0a4)"></div>
  <div class="slide" role="img" aria-label="Bright dining room with white furniture" style="left:189px;top:143px;width:110px;height:382px;background:linear-gradient(180deg,#f2f3f4,#dfe2e4 55%,#a8aeb2)"></div>
  <div class="slide" role="img" aria-label="White living room with sofa and lamp" style="left:911px;top:143px;width:110px;height:382px;background:linear-gradient(180deg,#efeeea,#d8d6d0 60%,#a9a6a0)"></div>
  <div class="slide" role="img" aria-label="Living room with a tall plant by a window" style="left:1009px;top:164px;width:86px;height:336px;background:linear-gradient(90deg,#b89b5e,#d8c79a 45%,#6c6a45)"></div>
  <div class="slide" role="img" aria-label="Featured property interior with booth seating, red cushions and pendant lights" style="left:287px;top:115px;width:624px;height:435px;background:
    radial-gradient(ellipse 120px 40px at 170px 60px,rgba(255,240,200,.9),transparent 70%),
    radial-gradient(ellipse 90px 70px at 500px 270px,rgba(200,60,70,.45),transparent 70%),
    linear-gradient(180deg,transparent 60%,rgba(120,110,105,.55) 100%),
    linear-gradient(90deg,#cfc9bf 0%,#ece8e1 40%,#e2ddd4 60%,#9a8f86 85%,#7a7371 100%)"></div>
  <div class="dots"><span></span><span></span><span></span></div>
</section>

<section class="team">
  <h2 class="sec-title">TEAM MEMBERS</h2>
  <svg class="arrow" style="left:92px" width="14" height="24" viewBox="0 0 14 24"><path d="M11 3 3 12l8 9" fill="none" stroke="#fff" stroke-width="2.5"/></svg>
  <svg class="arrow" style="left:1094px" width="14" height="24" viewBox="0 0 14 24"><path d="M3 3l8 9-8 9" fill="none" stroke="#fff" stroke-width="2.5"/></svg>
  <div class="member" style="left:131px"><div class="portrait" role="img" aria-label="Portrait photo of Liesel Marrow" style="background:radial-gradient(circle at 50% 40%,#d7b89c,#b88f6a 45%,#5e6a78 90%)"></div><h3>Liesel Marrow</h3><span>( CEO )</span></div>
  <div class="member" style="left:381px"><div class="portrait" role="img" aria-label="Portrait photo of Orrin" style="background:radial-gradient(circle at 50% 40%,#e0c1a6,#c79e80 40%,#3b4150 85%)"></div><h3>Orrin</h3><span>( President )</span></div>
  <div class="member" style="left:629px"><div class="portrait" role="img" aria-label="Portrait photo of Tamsin" style="background:radial-gradient(circle at 50% 40%,#d9b397,#7a4d36 55%,#e8e8e8 95%)"></div><h3>Tamsin</h3><span>( Partner )</span></div>
  <div class="member" style="left:877px"><div class="portrait" role="img" aria-label="Portrait photo of Pell Aster" style="background:radial-gradient(circle at 50% 40%,#e3bfa3,#cfa488 40%,#7da0c2 90%)"></div><h3>Pell Aster</h3><span>( Partner )</span></div>
</section>

<section class="news">
  <h2 class="sec-title" style="left:98px">LATEST BLOG</h2>
  <article class="post" style="left:98px;top:115px"><div class="thumb" role="img" aria-label="Business handshake at a desk" style="background:linear-gradient(135deg,#eef2f4,#b9c7d0 50%,#5f7584)"></div><h4>Nemo enim ipsam voluptatem quia voluptas sit aspernatur aut</h4><div class="meta"><i></i>23/01/2016 &nbsp;|&nbsp; <i></i>Pell Aster</div></article>
  <article class="post" style="left:98px;top:248px"><div class="thumb" role="img" aria-label="Empty bright hallway" style="background:linear-gradient(135deg,#f4efe6,#d6c6a9 55%,#8e7a5c)"></div><h4>Nemo enim ipsam voluptatem quia voluptas sit aspernatur aut</h4><div class="meta"><i></i>23/01/2016 &nbsp;|&nbsp; <i></i>Pell Aster</div></article>
  <article class="post last" style="left:98px;top:383px"><div class="thumb" role="img" aria-label="Handshake over signed papers" style="background:linear-gradient(135deg,#f1ece8,#d4b9a6 50%,#8a7fa0)"></div><h4>Nemo enim ipsam voluptatem quia voluptas sit aspernatur aut</h4><div class="meta"><i></i>23/01/2016 &nbsp;|&nbsp; <i></i>Pell Aster</div></article>
  <div class="view-more" style="left:478px">VIEW MORE &gt;&gt;</div>

  <h2 class="sec-title" style="left:636px">PRESS</h2>
  <article class="post" style="left:636px;top:115px"><div class="thumb" role="img" aria-label="Meeting around a table" style="background:linear-gradient(135deg,#eceff0,#c3ccd1 50%,#7b8a92)"></div><h4>Nemo enim ipsam voluptatem quia voluptas sit aspernatur aut</h4><div class="meta"><i></i>23/01/2016 &nbsp;|&nbsp; <i></i>Pell Aster</div></article>
  <article class="post" style="left:636px;top:248px"><div class="thumb" role="img" aria-label="Agents handing over keys" style="background:linear-gradient(135deg,#e5e7ea,#9ea5ab 50%,#3f464c)"></div><h4>Nemo enim ipsam voluptatem quia voluptas sit aspernatur aut</h4><div class="meta"><i></i>23/01/2016 &nbsp;|&nbsp; <i></i>Pell Aster</div></article>
  <article class="post last" style="left:636px;top:383px"><div class="thumb" role="img" aria-label="Bright white interior" style="background:linear-gradient(135deg,#f7f7f7,#d9d8dc 50%,#9c9aa2)"></div><h4>Nemo enim ipsam voluptatem quia voluptas sit aspernatur aut</h4><div class="meta"><i></i>23/01/2016 &nbsp;|&nbsp; <i></i>Pell Aster</div></article>
  <div class="view-more" style="left:1014px">VIEW MORE &gt;&gt;</div>
</section>

<section class="contact">
  <h2 class="sec-title">CONTACT US</h2>
  <h5 style="left:98px;top:113px">GET IN TOUCH</h5>
  <label style="top:152px">NAME :</label>
  <div class="input" style="top:181px;height:34px"></div>
  <label style="top:232px">EMAIL :</label>
  <div class="input" style="top:255px;height:34px"></div>
  <label style="top:306px">MESSAGE :</label>
  <div class="input" style="top:330px;height:81px"></div>
  <div class="send">SUBMIT</div>

  <h5 style="left:810px;top:113px">CONTACT INFORMATION</h5>
  <div class="info-icon" style="top:164px"><svg width="14" height="18" viewBox="0 0 14 18"><path d="M7 17S1 10 1 6.5a6 6 0 0 1 12 0C13 10 7 17 7 17z" fill="#fff"/><circle cx="7" cy="6.5" r="2.2" fill="#2c2c2c"/></svg></div>
  <div class="info-text" style="top:161px">482 Larkfield Row,<br>Suite 12,<br>Hollin Bay 40217</div>
  <div class="info-icon" style="top:250px"><svg width="16" height="12" viewBox="0 0 16 12"><rect width="16" height="12" rx="1.5" fill="#fff"/><path d="M1 1l7 6 7-6" fill="none" stroke="#2c2c2c" stroke-width="1.5"/></svg></div>
  <div class="info-text" style="top:256px">hello@velmoramanagement.example</div>
  <div class="info-icon" style="top:311px"><svg width="14" height="14" viewBox="0 0 14 14"><path d="M3 1l2.5 3-1.5 1.5c1 2 2.5 3.5 4.5 4.5L10 8.5l3 2.5-1.5 2C6 13 1 8 1 2.5z" fill="#fff"/></svg></div>
  <div class="info-text" style="top:318px">1 - 555 - 014 - 2290</div>
  <h5 style="left:810px;top:389px">SOCIAL</h5>
  <div class="social"><span></span><span></span><span></span><span></span></div>
  <div class="footer-rule"></div>
  <div class="copyright">Copyrights © 2016, Velmora Management . All Rights Reserved.</div>
</section>

</body>
</html>
```